New Business Card Design Project

Use the flyer uploaded and website www.brightoakbuilders.com for inspiration.
List Our Services on Backside of business cards
Marcus Delling
Harborline Builders Inc.
Licensed General Contractors
858-471-6093

Contact Information for Business Card

Use the flyer uploaded and website www.brightoakbuilders.com for inspiration. List Our Services on Backside of business cards Marcus Delling Harborline Builders Inc. Licensed General Contractors 858-471-6093

```html
<!DOCTYPE html>
<html lang="en">
<head>
<meta charset="UTF-8">
<title>Harborline Builders – Business Card</title>
<link rel="stylesheet" href="https://fonts.googleapis.com/css2?family=Lora:ital,wght@0,400;0,600;0,700;1,600&display=swap">
<style>
  :root {
    --page: #e9e6e1;
    --card: #111112;
    --ink: #f2f2f2;
    --ink-soft: #d9d9d9;
    --accent: #2f9fe0;
    --rule: #8a8a8a;
    --deco-a: #2a2a2c;
    --deco-b: #1a1a1b;
  }
  * { box-sizing: border-box; margin: 0; padding: 0; }
  html, body { width: 1200px; height: 900px; overflow: hidden; }
  body {
    background: var(--page);
    font-family: "Lora", Georgia, serif;
    color: var(--ink);
    display: flex;
    flex-direction: column;
    align-items: center;
    justify-content: center;
    gap: 36px;
  }
  .card {
    position: relative;
    width: 700px;
    height: 400px;
    background: var(--card);
    box-shadow: 0 10px 28px rgba(0,0,0,.25);
    overflow: hidden;
  }
  .brand {
    position: absolute;
    display: flex;
    align-items: center;
    gap: 12px;
    font-weight: 400;
    font-size: 25px;
    letter-spacing: 2px;
    text-transform: uppercase;
    color: var(--ink);
  }
  .brand__mark {
    width: 12px; height: 12px;
    border: 1.5px solid var(--ink);
    border-radius: 50%;
  }
  /* Back side */
  .card--services .brand { left: 60px; top: 182px; }
  .services {
    position: absolute;
    right: 40px;
    top: 70px;
    text-align: right;
  }
  .services__title {
    font-weight: 700;
    font-size: 22px;
    letter-spacing: 1px;
    color: var(--accent);
    margin-bottom: 6px;
    text-transform: uppercase;
  }
  .services__list { list-style: none; }
  .services__item {
    display: flex;
    justify-content: flex-end;
    align-items: center;
    gap: 10px;
    font-size: 15px;
    line-height: 25px;
    color: var(--ink);
  }
  .services__item svg { width: 15px; height: 15px; flex: none; }
  /* Front side */
  .card--contact .brand { right: 48px; top: 88px; }
  .decor {
    position: absolute;
    left: 40px; top: 60px;
    width: 300px; height: 300px;
    border-radius: 50%;
    background: radial-gradient(circle, var(--deco-a) 0%, var(--deco-b) 60%, transparent 72%);
  }
  .contact {
    position: absolute;
    left: 60px; top: 190px;
  }
  .contact__name {
    font-weight: 700;
    font-size: 24px;
    letter-spacing: 1.5px;
    text-transform: uppercase;
  }
  .contact__cta {
    font-style: italic;
    font-weight: 600;
    font-size: 20px;
    margin: 10px 0 8px;
  }
  .contact__row {
    display: flex; align-items: center; gap: 10px;
    font-size: 17px; line-height: 28px; color: var(--ink-soft);
  }
  .contact__row svg { width: 16px; height: 16px; flex: none; }
  .legal {
    position: absolute;
    left: 48px; right: 48px; bottom: 28px;
    border-top: 1px solid var(--rule);
    padding-top: 14px;
    font-size: 18px;
    color: var(--ink-soft);
  }
</style>
</head>
<body>

<section class="card card--services">
  <div class="brand"><span class="brand__mark"></span>Harborline Builders</div>
  <div class="services">
    <h2 class="services__title">Our Services</h2>
    <ul class="services__list">
      <li class="services__item">Remodel - Kitchen &amp; Bath <svg viewBox="0 0 16 16"><circle cx="8" cy="8" r="6.5" fill="none" stroke="#2f9fe0" stroke-width="1.5"/><path d="M5 8.2l2 2 4-4" fill="none" stroke="#2f9fe0" stroke-width="1.5"/></svg></li>
      <li class="services__item">Painting - Interior &amp; Exterior <svg viewBox="0 0 16 16"><circle cx="8" cy="8" r="6.5" fill="none" stroke="#2f9fe0" stroke-width="1.5"/><path d="M5 8.2l2 2 4-4" fill="none" stroke="#2f9fe0" stroke-width="1.5"/></svg></li>
      <li class="services__item">Flooring - Carpet, Vinyl, Wood <svg viewBox="0 0 16 16"><circle cx="8" cy="8" r="6.5" fill="none" stroke="#2f9fe0" stroke-width="1.5"/><path d="M5 8.2l2 2 4-4" fill="none" stroke="#2f9fe0" stroke-width="1.5"/></svg></li>
      <li class="services__item">Window &amp; Door Replacement <svg viewBox="0 0 16 16"><circle cx="8" cy="8" r="6.5" fill="none" stroke="#2f9fe0" stroke-width="1.5"/><path d="M5 8.2l2 2 4-4" fill="none" stroke="#2f9fe0" stroke-width="1.5"/></svg></li>
      <li class="services__item">Plumbing - Repairs &amp; Upgrades <svg viewBox="0 0 16 16"><circle cx="8" cy="8" r="6.5" fill="none" stroke="#2f9fe0" stroke-width="1.5"/><path d="M5 8.2l2 2 4-4" fill="none" stroke="#2f9fe0" stroke-width="1.5"/></svg></li>
      <li class="services__item">Energy - Efficient Upgrades <svg viewBox="0 0 16 16"><circle cx="8" cy="8" r="6.5" fill="none" stroke="#2f9fe0" stroke-width="1.5"/><path d="M5 8.2l2 2 4-4" fill="none" stroke="#2f9fe0" stroke-width="1.5"/></svg></li>
      <li class="services__item">Deck &amp; Patio Construction <svg viewBox="0 0 16 16"><circle cx="8" cy="8" r="6.5" fill="none" stroke="#2f9fe0" stroke-width="1.5"/><path d="M5 8.2l2 2 4-4" fill="none" stroke="#2f9fe0" stroke-width="1.5"/></svg></li>
      <li class="services__item">Water &amp; Mold Damage <svg viewBox="0 0 16 16"><circle cx="8" cy="8" r="6.5" fill="none" stroke="#2f9fe0" stroke-width="1.5"/><path d="M5 8.2l2 2 4-4" fill="none" stroke="#2f9fe0" stroke-width="1.5"/></svg></li>
      <li class="services__item">Garage Renovation <svg viewBox="0 0 16 16"><circle cx="8" cy="8" r="6.5" fill="none" stroke="#2f9fe0" stroke-width="1.5"/><path d="M5 8.2l2 2 4-4" fill="none" stroke="#2f9fe0" stroke-width="1.5"/></svg></li>
    </ul>
  </div>
</section>

<section class="card card--contact">
  <div class="decor" role="img" aria-label="Faint decorative tree motif in dark grey"></div>
  <div class="brand"><span class="brand__mark"></span>Harborline Builders</div>
  <div class="contact">
    <h1 class="contact__name">Marcus Delling</h1>
    <p class="contact__cta">Call/Text Or Book Online</p>
    <p class="contact__row"><svg viewBox="0 0 16 16"><path d="M4 1.5l2.5 3-1.5 1.5a8 8 0 0 0 5 5l1.5-1.5 3 2.5-1.5 2.5C7 14 2 9 1.5 3z" fill="#d9d9d9"/></svg>858-471-6093</p>
    <p class="contact__row"><svg viewBox="0 0 16 16" fill="none" stroke="#d9d9d9" stroke-width="1.2"><circle cx="8" cy="8" r="6.5"/><ellipse cx="8" cy="8" rx="3" ry="6.5"/><path d="M1.5 8h13M2.5 4.8h11M2.5 11.2h11"/></svg>www.brightoakbuilders.com</p>
  </div>
  <p class="legal">Harborline Builders Inc. - Licensed General Contractors</p>
</section>

</body>
</html>
```